Verodex business card

Business card for sustainable investment company called "Verodex". Verodex is an exchange platform selling carbon credits between buyers and sellers. Carbon Credits are an environmental commodity for reducing global carbon emissions.

the card should obviously have our logo and the theme should be sustainability/environment mixed with a trading platform.

Contact Information for Business Card

Logo, Name, Title, Phone, Email

Colors
0054AA
0677BA
7BADD7
CADEEF
E8F1F8
0094D4
00A9DD
6FCCEA
C7EBF8
E9F6FB
00AB8E
00BBA5
67D7C9
C6EFE9
E9F9F6
59FF00
82FF00
B8FF75
E3FFCB
F4FFEA

```html
<!DOCTYPE html>
<html lang="en">
<head>
<meta charset="utf-8">
<title>Verodex business card</title>
<link rel="stylesheet" href="https://fonts.googleapis.com/css2?family=Montserrat:wght@600;700&family=Open+Sans:wght@400;600&display=swap">
<style>
  :root {
    --bg: #dcdde0;
    --paper: #ffffff;
    --navy: #152c55;
    --navy-deep: #10244a;
    --blue: #3f7fcb;
    --sky: #5cc0dd;
    --ink: #152c55;
    --muted: #4a5568;
    --icon: #3f9bd6;
  }
  html, body {
    margin: 0;
    padding: 0;
    width: 1200px;
    height: 800px;
    overflow: hidden;
    background: var(--bg);
  }
  .canvas {
    position: relative;
    width: 1200px;
    height: 800px;
    display: flex;
    align-items: center;
    justify-content: center;
    gap: 50px;
  }
  .card {
    position: relative;
    width: 525px;
    height: 300px;
    background: var(--paper);
    overflow: hidden;
    box-shadow: 0 10px 24px rgba(20, 30, 50, 0.18);
  }
  .card-art {
    position: absolute;
    inset: 0;
    width: 100%;
    height: 100%;
  }
  .wordmark {
    position: absolute;
    display: flex;
    align-items: center;
    gap: 12px;
    font-family: "Montserrat", sans-serif;
    font-weight: 700;
    color: var(--ink);
    letter-spacing: 0.02em;
  }
  .wordmark-dot {
    width: 14px;
    height: 14px;
    background: var(--blue);
  }
  .front .wordmark { top: 40px; left: 34px; font-size: 38px; }
  .back .wordmark { left: 170px; top: 180px; font-size: 38px; }
  .contact {
    position: absolute;
    left: 34px;
    top: 130px;
    font-family: "Open Sans", sans-serif;
    color: var(--muted);
  }
  .contact-name {
    margin: 0;
    font-family: "Montserrat", sans-serif;
    font-weight: 700;
    font-size: 15px;
    color: var(--ink);
    letter-spacing: 0.04em;
  }
  .contact-title {
    margin: 2px 0 18px;
    font-size: 13px;
  }
  .contact-line {
    display: flex;
    align-items: center;
    gap: 8px;
    font-size: 13px;
    margin: 0 0 6px;
  }
  .contact-line svg { width: 12px; height: 12px; fill: var(--icon); }
</style>
</head>
<body>
<main class="canvas">

  <section class="card front" aria-label="Card front">
    <svg class="card-art" viewBox="0 0 525 300" preserveAspectRatio="none" aria-hidden="true">
      <defs>
        <linearGradient id="front-fold" x1="0" y1="1" x2="1" y2="0">
          <stop offset="0" stop-color="var(--blue)"/>
          <stop offset="1" stop-color="var(--sky)"/>
        </linearGradient>
      </defs>
      <polygon points="455,0 525,0 525,300 190,300" fill="var(--navy)"/>
      <polygon points="405,0 455,0 478,120 190,300 176,300 420,105" fill="url(#front-fold)"/>
    </svg>
    <div class="wordmark"><span class="wordmark-dot"></span>VERODEX</div>
    <div class="contact">
      <p class="contact-name">DANIEL MARSH</p>
      <p class="contact-title">Director</p>
      <p class="contact-line">
        <svg viewBox="0 0 24 24"><path d="M6.6 10.8a15.1 15.1 0 0 0 6.6 6.6l2.2-2.2c.3-.3.7-.4 1-.2 1.1.4 2.3.6 3.6.6.6 0 1 .4 1 1V20c0 .6-.4 1-1 1A17 17 0 0 1 3 4c0-.6.4-1 1-1h3.5c.6 0 1 .4 1 1 0 1.3.2 2.5.6 3.6.1.3 0 .7-.2 1z"/></svg>
        300-555-0147
      </p>
      <p class="contact-line">
        <svg viewBox="0 0 24 24"><path d="M2 5h20v14H2zm2 2v.5l8 5 8-5V7z"/></svg>
        info@verodex.com
      </p>
    </div>
  </section>

  <section class="card back" aria-label="Card back">
    <svg class="card-art" viewBox="0 0 525 300" preserveAspectRatio="none" aria-hidden="true">
      <defs>
        <linearGradient id="back-fold" x1="0" y1="1" x2="1" y2="0">
          <stop offset="0" stop-color="var(--sky)"/>
          <stop offset="1" stop-color="var(--blue)"/>
        </linearGradient>
      </defs>
      <polygon points="0,0 300,0 0,0" fill="var(--navy)"/>
      <polygon points="0,0 0,0 310,0 0,300" fill="var(--navy)"/>
      <polygon points="0,0 330,0 0,290" fill="var(--navy-deep)" opacity="0"/>
      <polygon points="310,0 340,0 100,150 120,300 100,300 70,155" fill="url(#back-fold)"/>
      <polygon points="0,0 310,0 70,155 100,300 0,300" fill="var(--navy)"/>
    </svg>
    <div class="wordmark"><span class="wordmark-dot"></span>VERODEX</div>
  </section>

</main>
</body>
</html>
```